Interior Design/ New Construction interior finishes

Interior Design Website

Target Market(s)

Home builders, New Construction, Renovations, Public

Industry/Entity Type

Construction

Coding

Coded - Design and coding required

Number of Pages Required

1 page

Font styles to use
Sans Serif

Colors

Designer to choose colors to be used in the design.

Requirements
Must have
• Section to upload pictures of projects
• Simple and modern design
• Designer 1 details about myself
• Logo
• Upload section for photos for future jobs
Nice to have
• Sections they can click on to see certain rooms in a house
• Decorating, floral arrangements, holiday decorating.
• I have lots of before and after as well. Maybe a section for those.

```html
<!DOCTYPE html>
<html lang="en">
<head>
<meta charset="utf-8">
<title>Lumen Designs – Interior business &amp; new construction company</title>
<link href="https://fonts.googleapis.com/css2?family=Josefin+Sans:wght@600;700&family=Lato:ital,wght@0,400;0,700;1,400&display=swap" rel="stylesheet">
<style>
:root{
  --accent:#f5a800;
  --accent-dark:#e39400;
  --ink:#2b2b2b;
  --muted:#777;
  --white:#fff;
  --slate:#4c4f66;
  --night:#2a2a30;
  --footer:#262629;
  --line:#dcdcdc;
}
*{box-sizing:border-box;margin:0;padding:0}
html,body{width:1200px;height:3455px;overflow:hidden}
body{position:relative;background:var(--white);font-family:"Lato",sans-serif;color:var(--ink)}
.abs{position:absolute}
.heading{font-family:"Josefin Sans",sans-serif;font-weight:700}
.photo{position:absolute}

/* header */
.site-header{left:0;top:0;width:1200px;height:98px;background:var(--white);border-top:5px solid var(--accent);z-index:3}
.brand{left:95px;top:-5px;width:200px;height:165px;background:var(--white);border-radius:0 0 100px 100px;z-index:4;display:flex;flex-direction:column;align-items:center;justify-content:center;padding-top:10px}
.brand-mark{width:46px;height:46px;border:3px solid var(--ink);border-radius:50%;margin-bottom:8px}
.brand-name{font-family:"Lato",sans-serif;font-size:19px;font-weight:700;letter-spacing:1px;color:var(--ink)}
.nav{z-index:4;top:40px;left:0;width:1200px;font-size:15px;color:#555}
.nav span{position:absolute;transform:translateX(-50%);white-space:nowrap}
.nav .current{color:var(--accent)}

/* hero */
.hero{left:0;top:98px;width:1200px;height:547px;background:linear-gradient(180deg,#5b5a5c 0%,#7c6f68 45%,#8b4a3f 80%,#a32a28 100%)}
.hero-title{left:0;width:1200px;top:228px;text-align:center;color:var(--white);font-size:84px;z-index:2}
.hero-sub{left:0;width:1200px;top:330px;text-align:center;color:var(--white);font-size:23px;font-weight:700;z-index:2}
.btn{display:flex;align-items:center;justify-content:center;background:var(--accent);color:var(--white);font-weight:700;font-size:14px;border-radius:24px;letter-spacing:.5px}
.hero-btn{left:522px;top:385px;width:156px;height:46px;z-index:2}
.round-arrow{width:44px;height:44px;border:2px solid var(--white);border-radius:50%;z-index:2}

/* services */
.service-pic{width:276px;height:276px;border-radius:50%;border:5px solid var(--white);box-shadow:0 2px 8px rgba(0,0,0,.25);z-index:2}
.service-title{width:320px;text-align:center;font-size:23px;font-weight:700;color:var(--ink);top:792px}
.service-text{width:290px;text-align:center;font-size:13.5px;line-height:24px;color:var(--muted);top:825px}
.chev{top:906px;z-index:2}

/* about */
.about{left:0;top:1000px;width:1200px;height:504px;background:linear-gradient(135deg,#55586f,#464a60)}
.video-frame{left:94px;top:1082px;width:516px;height:339px;border:1px solid rgba(255,255,255,.45);padding:10px}
.video-frame .photo{position:relative;width:100%;height:100%;background:linear-gradient(135deg,#6a4a38,#b57b4f 50%,#4d3a30)}
.about-title{left:656px;top:1090px;color:var(--white);font-size:40px}
.about-text{left:656px;top:1146px;width:510px;color:#e6e6ee;font-size:13.5px;line-height:25px}
.about-text p+p{margin-top:8px}
.about-btn{left:656px;top:1371px;width:128px;height:40px}

/* before & after */
.section-title{left:0;width:1200px;text-align:center;font-size:36px;color:var(--ink)}
.ba-pic{top:1651px;width:228px;height:261px;box-shadow:0 6px 8px rgba(0,0,0,.2)}
.ba-label{top:1927px;width:228px;text-align:center;font-size:17px;font-weight:700;letter-spacing:1px;color:#333}
.ghost-arrow{width:40px;height:40px;border:1px solid #ccc;border-radius:50%;top:1763px}

/* testimonials */
.testimonials{left:0;top:2020px;width:1200px;height:421px;background:linear-gradient(180deg,#3a3533,#2b2927)}
.quote-text{left:195px;top:2235px;width:810px;text-align:center;font-style:italic;font-size:15px;line-height:26px;color:#eee}
.quote-name{left:0;width:1200px;top:2326px;text-align:center;color:var(--white);font-weight:700;font-size:17px}

/* projects */
.project{top:2618px;width:251px;height:226px}
.strip-arrow{width:28px;height:28px;background:rgba(0,0,0,.55);top:2717px}

/* contact */
.contact{left:0;top:2943px;width:1200px;height:512px;background:var(--footer);border-top:5px solid var(--accent)}
.sub-title{font-size:19px;font-weight:700;color:var(--white)}
.field{background:var(--white);border:1px solid #999;font-size:11px;color:#555;padding:8px 12px;letter-spacing:.5px}
.submit{left:626px;top:3307px;width:77px;height:26px;font-size:12px;border-radius:14px}
.info-icon{width:30px;height:30px;border:2px solid var(--accent);border-radius:50%;left:784px}
.info-text{left:838px;color:#ddd;font-size:13px;line-height:24px;width:260px}
.social{top:3303px;width:26px;height:26px;border-radius:50%;background:#555}
.divider{left:97px;top:3374px;width:1006px;height:1px;background:#4a4a4e}
.legal{left:0;width:1200px;top:3405px;text-align:center;color:#ccc;font-size:12px}
</style>
</head>
<body>

<header class="site-header abs"></header>
<div class="brand abs">
  <div class="brand-mark"></div>
  <div class="brand-name">Lumen Designs</div>
</div>
<nav class="nav abs">
  <span class="current" style="left:438px">Home</span>
  <span style="left:534px">About Us</span>
  <span style="left:636px">Services</span>
  <span style="left:728px">Gallery</span>
  <span style="left:822px">Projects</span>
  <span style="left:910px">News</span>
  <span style="left:1009px">Contact Us</span>
  <span style="left:1094px;top:-1px">
    <svg width="15" height="15" viewBox="0 0 15 15"><circle cx="6" cy="6" r="4.5" fill="none" stroke="#333" stroke-width="2"/><line x1="9.5" y1="9.5" x2="13.5" y2="13.5" stroke="#333" stroke-width="2.2"/></svg>
  </span>
</nav>

<section class="hero abs" role="img" aria-label="Photo of a renovated home basketball court with wooden floor"></section>
<h1 class="hero-title heading abs">Lumen Designs</h1>
<p class="hero-sub abs">Interior business &amp; new construction company</p>
<a class="hero-btn btn abs">GET STARTED</a>
<div class="round-arrow abs" style="left:20px;top:312px"><svg width="40" height="40" viewBox="0 0 40 40"><polyline points="23,13 16,20 23,27" fill="none" stroke="#fff" stroke-width="2.5"/></svg></div>
<div class="round-arrow abs" style="left:1134px;top:312px"><svg width="40" height="40" viewBox="0 0 40 40"><polyline points="17,13 24,20 17,27" fill="none" stroke="#fff" stroke-width="2.5"/></svg></div>

<div class="service-pic photo" style="left:104px;top:500px;background:radial-gradient(circle at 50% 40%,#c7956a,#6e4a36)" role="img" aria-label="Photo of a decorated living room"></div>
<div class="service-pic photo" style="left:462px;top:500px;background:radial-gradient(circle at 50% 45%,#b8a6d8,#d9d6d2 60%,#8b8a88)" role="img" aria-label="Photo of a floral arrangement on a table"></div>
<div class="service-pic photo" style="left:818px;top:500px;background:radial-gradient(circle at 50% 50%,#e08a3a,#6a4a2c 55%,#2d2420)" role="img" aria-label="Photo of a holiday table setting"></div>

<h3 class="service-title abs" style="left:82px">Decorating</h3>
<h3 class="service-title abs" style="left:440px">Floral Arrangements</h3>
<h3 class="service-title abs" style="left:796px">Holiday Decorating</h3>
<p class="service-text abs" style="left:97px">Sed ut perspiciatis unde omnis iste natus error sit voluptatem accusantium dolorem-que laudantiumtotam rem aperiam</p>
<p class="service-text abs" style="left:455px">Sed ut perspiciatis unde omnis iste natus error sit voluptatem accusantium dolorem-que laudantiumtotam rem aperiam</p>
<p class="service-text abs" style="left:811px">Sed ut perspiciatis unde omnis iste natus error sit voluptatem accusantium dolorem-que laudantiumtotam rem aperiam</p>
<svg class="chev abs" style="left:233px" width="18" height="18" viewBox="0 0 18 18"><polyline points="3,3 9,8 15,3" fill="none" stroke="#f5a800" stroke-width="2.2"/><polyline points="3,9 9,14 15,9" fill="none" stroke="#f5a800" stroke-width="2.2"/></svg>
<svg class="chev abs" style="left:591px" width="18" height="18" viewBox="0 0 18 18"><polyline points="3,3 9,8 15,3" fill="none" stroke="#f5a800" stroke-width="2.2"/><polyline points="3,9 9,14 15,9" fill="none" stroke="#f5a800" stroke-width="2.2"/></svg>
<svg class="chev abs" style="left:947px" width="18" height="18" viewBox="0 0 18 18"><polyline points="3,3 9,8 15,3" fill="none" stroke="#f5a800" stroke-width="2.2"/><polyline points="3,9 9,14 15,9" fill="none" stroke="#f5a800" stroke-width="2.2"/></svg>

<section class="about abs"></section>
<div class="video-frame abs">
  <div class="photo" role="img" aria-label="Video still of an open-plan living and dining room with wooden beams"></div>
</div>
<svg class="abs" style="left:320px;top:1219px" width="64" height="64" viewBox="0 0 64 64"><circle cx="32" cy="32" r="31" fill="#e0241f"/><polygon points="25,19 46,32 25,45" fill="#fff"/></svg>
<h2 class="about-title heading abs">About Us</h2>
<div class="about-text abs">
  <p>At vero eos et accusamus et iusto odio dignissimos ducimus qui blanditiis praesentium voluptatum deleniti atque corrupti quos dolores et quas molestias excepturi sint occaecati cupiditate non provident, similique sunt in culpa qui officia deserunt mollitia animi.</p>
  <p>Et harum quidem rerum facilis est et expedita distinctio. Nam libero tempore, cum soluta nobis est eligendi optio cumque nihil impedit quo minus id quod maxime placeat facere possimus, omnis voluptas assumenda est, omnis dolor repellendus.</p>
</div>
<a class="about-btn btn abs">READ MORE</a>

<h2 class="section-title heading abs" style="top:1570px">Before &amp; After</h2>
<div class="ghost-arrow abs" style="left:50px"><svg width="38" height="38" viewBox="0 0 38 38"><polyline points="22,13 16,19 22,25" fill="none" stroke="#bbb" stroke-width="2"/></svg></div>
<div class="ghost-arrow abs" style="left:1109px"><svg width="38" height="38" viewBox="0 0 38 38"><polyline points="16,13 22,19 16,25" fill="none" stroke="#bbb" stroke-width="2"/></svg></div>
<div class="ba-pic photo" style="left:117px;background:linear-gradient(180deg,#6b6763,#3f3a36)" role="img" aria-label="Kitchen before renovation"></div>
<div class="ba-pic photo" style="left:357px;background:linear-gradient(180deg,#f3e6c8,#d8cab0)" role="img" aria-label="Kitchen after renovation"></div>
<div class="ba-pic photo" style="left:613px;background:linear-gradient(180deg,#e3e3e0,#c6c3bd)" role="img" aria-label="Dining room before renovation"></div>
<div class="ba-pic photo" style="left:854px;background:linear-gradient(180deg,#a93228,#7a3b2c)" role="img" aria-label="Dining room after renovation"></div>
<div class="ba-label abs" style="left:117px">BEFORE</div>
<div class="ba-label abs" style="left:357px">AFTER</div>
<div class="ba-label abs" style="left:613px">BEFORE</div>
<div class="ba-label abs" style="left:854px">AFTER</div>

<section class="testimonials abs" role="img" aria-label="Dim photo of a living room interior behind client reviews"></section>
<div class="abs" style="left:72px;top:2040px;width:1056px;height:401px;background:rgba(40,38,36,.45)"></div>
<h2 class="section-title heading abs" style="top:2112px;color:#fff">What Clients Say</h2>
<svg class="abs" style="left:570px;top:2170px" width="60" height="50" viewBox="0 0 60 50"><path d="M4 48V28C4 14 10 6 24 2v8c-7 3-9 8-9 14h9v24zM34 48V28C34 14 40 6 54 2v8c-7 3-9 8-9 14h9v24z" fill="#f5a800"/></svg>
<svg class="abs" style="left:68px;top:2195px" width="36" height="70" viewBox="0 0 36 70"><polyline points="32,3 4,35 32,67" fill="none" stroke="#fff" stroke-width="2"/></svg>
<svg class="abs" style="left:1096px;top:2195px" width="36" height="70" viewBox="0 0 36 70"><polyline points="4,3 32,35 4,67" fill="none" stroke="#fff" stroke-width="2"/></svg>
<p class="quote-text abs">At vero eos et accusamus et iusto odio dignissimos ducimus qui blanditiis praesentium voluptatum deleniti atque corrupti quos dolores et quas molestias excepturi sint occaecati cupiditate non provident, similique sunt in culpa qui officia deserunt mollitia animi, id est laborum et harum quidem rerum facilis est et expedita distinctio.</p>
<div class="quote-name abs">- OFFICIIS DEBITIS &nbsp;<span style="color:var(--accent);font-size:22px;letter-spacing:2px">★★★★★</span></div>

<h2 class="section-title heading abs" style="top:2537px">Our Projects</h2>
<div class="project photo" style="left:99px;background:linear-gradient(135deg,#c9b8a4,#7a6552)" role="img" aria-label="Project photo: children's loft bedroom"></div>
<div class="project photo" style="left:350px;background:linear-gradient(135deg,#3c3d44,#8b7a66)" role="img" aria-label="Project photo: dining room with chandelier"></div>
<div class="project photo" style="left:601px;background:linear-gradient(135deg,#d9dcdf,#a6a19a)" role="img" aria-label="Project photo: breakfast nook"></div>
<div class="project photo" style="left:852px;width:249px;background:linear-gradient(135deg,#d9a640,#8a6420)" role="img" aria-label="Project photo: living room with golden light"></div>
<div class="strip-arrow abs" style="left:102px"><svg width="28" height="28" viewBox="0 0 28 28"><polyline points="16,9 11,14 16,19" fill="none" stroke="#fff" stroke-width="2.2"/></svg></div>
<div class="strip-arrow abs" style="left:1070px"><svg width="28" height="28" viewBox="0 0 28 28"><polyline points="12,9 17,14 12,19" fill="none" stroke="#fff" stroke-width="2.2"/></svg></div>

<section class="contact abs"></section>
<h2 class="section-title heading abs" style="top:3015px;color:#fff">Contact Us</h2>
<h4 class="sub-title abs" style="left:97px;top:3086px">Get In Touch:</h4>
<div class="field abs" style="left:99px;top:3130px;width:297px;height:32px">NAME :</div>
<div class="field abs" style="left:408px;top:3130px;width:295px;height:32px">PHONE :</div>
<div class="field abs" style="left:99px;top:3176px;width:604px;height:32px">EMAIL :</div>
<div class="field abs" style="left:99px;top:3220px;width:604px;height:69px">MESSAGE :</div>
<a class="submit btn abs">SUBMIT</a>

<h4 class="sub-title abs" style="left:783px;top:3086px">Contact Information</h4>
<div class="info-icon abs" style="top:3135px"><svg width="26" height="26" viewBox="0 0 26 26"><path d="M13 5a5 5 0 0 0-5 5c0 4 5 10 5 10s5-6 5-10a5 5 0 0 0-5-5z" fill="#f5a800"/><circle cx="13" cy="10" r="2" fill="#262629"/></svg></div>
<div class="info-icon abs" style="top:3193px"><svg width="26" height="26" viewBox="0 0 26 26"><path d="M8 6l3 0 1 4-2 1c1 2 2 3 4 4l1-2 4 1v3c-6 1-12-5-11-11z" fill="#f5a800"/></svg></div>
<div class="info-icon abs" style="top:3246px"><svg width="26" height="26" viewBox="0 0 26 26"><rect x="6" y="8" width="14" height="10" fill="#f5a800"/><polyline points="6,8 13,14 20,8" fill="none" stroke="#262629" stroke-width="1.4"/></svg></div>
<p class="info-text abs" style="top:3126px">312,Nam libero temporesoluta nobis est eligendi optio cumque.</p>
<p class="info-text abs" style="top:3196px">1 555 010 0199</p>
<p class="info-text abs" style="top:3249px">info@lumendesigns.com</p>
<div class="social abs" style="left:787px"></div>
<div class="social abs" style="left:821px"></div>
<div class="social abs" style="left:855px"></div>
<div class="social abs" style="left:889px"></div>

<div class="divider abs"></div>
<p class="legal abs">Copyrights © 2018, Lumen Designs.All Rights Reserved. &nbsp;| &nbsp;Privacy policy</p>

</body>
</html>
```